BUSINESS CARD DESIGN

NAME- DALE VORSKIN
PHONE NUMER - 555- 714-9082
EMAIL- OFFICE@TRV-GROUNDMAKRZ.COM
BACK OF CARD- SPEACIALIZES IN LAND CLEARING, FORESTRY MUCLHING AND EXCAVATION

Contact Information for Business Card

NAME- DALE VORSKIN PHONE NUMER - 555- 714-9082 EMAIL- OFFICE@TRV-GROUNDMAKRZ.COM BACK OF CARD- SPEACIALIZES IN LAND CLEARING , MUCLHING AND EXCAVATION

```html
<!DOCTYPE html>
<html lang="en">
<head>
<meta charset="utf-8">
<title>Trivale Groundmakrz – Business Card</title>
<link href="https://fonts.googleapis.com/css2?family=Lato:wght@400;700;900&display=swap" rel="stylesheet">
<style>
  :root {
    --stage: #3a3a3c;
    --ink: #0d0d0d;
    --card-dark: #1a1a1b;
    --paper: #ffffff;
    --silver: #e4e4e6;
    --muted: #bdbdbf;
  }
  * { box-sizing: border-box; margin: 0; padding: 0; }
  html, body { width: 1200px; height: 694px; overflow: hidden; }
  body {
    background: var(--stage);
    font-family: "Lato", sans-serif;
    position: relative;
  }
  .card {
    position: absolute;
    top: 187px;
    width: 560px;
    height: 320px;
    border-radius: 18px;
    overflow: hidden;
  }
  .card-back { left: 27px; background: var(--card-dark); color: var(--silver); }
  .card-front { left: 613px; background: var(--paper); color: var(--ink); }

  .brand {
    display: flex;
    align-items: center;
    gap: 10px;
    font-weight: 900;
    letter-spacing: 1px;
    line-height: 1.1;
    white-space: nowrap;
  }
  .brand-dot { width: 16px; height: 16px; border-radius: 50%; background: currentColor; flex: none; }
  .brand-name { text-transform: uppercase; }

  .card-back .brand { position: absolute; left: 0; right: 0; top: 110px; justify-content: center; font-size: 28px; }
  .card-back .brand-phone {
    position: absolute; left: 0; right: 0; top: 155px; text-align: center;
    font-size: 15px; font-weight: 400; letter-spacing: 6px; color: var(--muted);
  }
  .tagline {
    position: absolute; left: 0; right: 0; bottom: 46px; text-align: center;
    font-size: 17px; color: var(--paper);
  }
  .back-fold { position: absolute; left: 34px; top: 0; bottom: 0; width: 1px; background: #2c2c44; }

  .wave { position: absolute; inset: 0; width: 100%; height: 100%; }
  .card-front .brand { position: absolute; left: 30px; top: 118px; font-size: 17px; color: var(--ink); }
  .card-front .brand-dot { width: 11px; height: 11px; }
  .card-front .brand-phone {
    position: absolute; left: 30px; top: 146px; font-size: 11px; letter-spacing: 4px; font-weight: 700;
  }
  .holder { position: absolute; right: 40px; top: 26px; text-align: right; }
  .holder-name { font-size: 24px; font-weight: 900; letter-spacing: -0.5px; line-height: 1.2; }
  .holder-role { font-size: 14px; margin-top: 2px; line-height: 1.2; }
  .holder-bar { position: absolute; right: 0; top: 22px; width: 12px; height: 54px; background: var(--ink); }

  .contact {
    position: absolute; right: 22px; top: 160px; list-style: none;
    color: var(--paper); font-size: 14px; text-align: right; line-height: 21px;
  }
  .contact li { display: flex; justify-content: flex-end; align-items: center; gap: 8px; }
  .contact svg { width: 13px; height: 13px; fill: var(--paper); flex: none; }
  .contact .address { margin-top: 8px; padding-right: 21px; display: block; }
</style>
</head>
<body>
  <section class="card card-back">
    <div class="back-fold"></div>
    <div class="brand"><span class="brand-dot"></span><span class="brand-name">Trivale Groundmakrz</span></div>
    <div class="brand-phone">555-714-9082</div>
    <p class="tagline">Speacializes In Land Clearing , Muclhing And Excavation</p>
  </section>

  <section class="card card-front">
    <svg class="wave" viewBox="0 0 560 320" preserveAspectRatio="none" aria-hidden="true">
      <path d="M0 288 C110 298 215 268 272 205 C315 155 360 120 430 100 C375 130 335 175 298 228 C240 300 120 314 0 304 Z" fill="var(--ink)"/>
      <path d="M165 320 C245 300 285 230 318 165 C350 112 440 96 560 92 L560 300 Q560 320 540 320 Z" fill="var(--ink)"/>
    </svg>
    <div class="brand"><span class="brand-dot"></span><span class="brand-name">Trivale Groundmakrz</span></div>
    <div class="brand-phone">555-714-9082</div>
    <div class="holder-bar"></div>
    <div class="holder">
      <div class="holder-name">DALE VORSKIN</div>
      <div class="holder-role">Owner</div>
    </div>
    <ul class="contact">
      <li>555- 714-9082 <svg viewBox="0 0 24 24"><path d="M6.6 10.8a15 15 0 0 0 6.6 6.6l2.2-2.2c.3-.3.7-.4 1-.2 1.1.4 2.3.6 3.6.6.6 0 1 .4 1 1V20c0 .6-.4 1-1 1A17 17 0 0 1 3 4c0-.6.4-1 1-1h3.5c.6 0 1 .4 1 1 0 1.3.2 2.5.6 3.6.1.3 0 .7-.2 1z"/></svg></li>
      <li>Office@trv-groundmakrz.com <svg viewBox="0 0 24 24"><path d="M2 5h20v14H2z M2 5l10 8 10-8" fill="none" stroke="#fff" stroke-width="2"/></svg></li>
      <li>www.websitename.com <svg viewBox="0 0 24 24"><circle cx="12" cy="12" r="10"/></svg></li>
      <li class="address">421, Address line goes here<br>45452, Country name</li>
    </ul>
  </section>
</body>
</html>
```